Modern Verdell Tree Care Website

I need a website for a full service Tree Care company. The company provides tree pruning, tree removal, tree preservation, emergency services, stump grinding, and emergency tree services.

Target Market(s)

Customers that need tree services

Industry/Entity Type

Landscaping, Tree Services

Coding

Coded - Design and coding required

Number of Pages Required

5+ page

Font styles to use
Sans Serif

Requirements
Must have
• Good clean design that showcases the services the company provides.
Nice to have
• Services page; contact form, blog, home page, about page

```html
<!DOCTYPE html>
<html lang="en">
<head>
<meta charset="utf-8">
<title>Verdell Tree Care</title>
<link href="https://fonts.googleapis.com/css2?family=Michroma&family=Montserrat:wght@400;500;600;700&display=swap" rel="stylesheet">
<style>
:root{
  --green:#7cbc3a;
  --green-dark:#2f4a1a;
  --slate:#4d5a5c;
  --orange:#fbb03b;
  --cream:#f3f5dc;
  --cream-deep:#e6ebcc;
  --brown:#7a5229;
  --text:#5b6157;
  --white:#ffffff;
}
*{margin:0;padding:0;box-sizing:border-box}
html,body{width:1200px;height:4227px;overflow:hidden;background:var(--white)}
body{position:relative;font-family:"Montserrat",sans-serif;color:var(--text)}
.abs{position:absolute}
.display{font-family:"Michroma",sans-serif;text-transform:uppercase;letter-spacing:-1px}
.btn{position:absolute;display:flex;align-items:center;justify-content:center;border-radius:30px;background:var(--orange);color:var(--white);font-weight:700;font-size:12px;text-transform:uppercase;text-decoration:none}

/* header */
.hero-bg{left:0;top:0;width:1200px;height:1180px;background:linear-gradient(180deg,#8fc1e6 0%,#b8d9ef 40%,#e9f3fa 60%,#ffffff 75%)}
.logo{left:87px;top:20px;display:flex;align-items:center;gap:14px}
.logo-mark{width:54px;height:54px;border-radius:50%;background:var(--green)}
.logo-name{font-family:"Michroma",sans-serif;font-size:24px;color:var(--slate);line-height:1.1}
.nav{top:38px;left:424px;display:flex;gap:0;font-size:13px;font-weight:500;color:var(--slate);text-transform:uppercase}
.nav a{position:absolute;white-space:nowrap;color:inherit;text-decoration:none}
.hero-title{left:0;width:1200px;top:150px;text-align:center;font-size:56px;line-height:64px;color:var(--slate)}
.hero-sub{left:0;width:1200px;top:292px;text-align:center;font-size:22px;color:var(--slate)}

/* about */
.about-photo{left:143px;top:726px;width:404px;height:407px;background:linear-gradient(135deg,#5b8a2e,#9dbf5e 50%,#6f7f62);clip-path:polygon(0 0,100% 0,100% 100%,0 100%)}
.about-title{left:609px;top:814px;font-size:34px;color:var(--green-dark)}
.about-text{left:609px;top:870px;width:440px;font-size:14px;line-height:22px}
.about-text p{margin-bottom:14px}

/* services */
.services{left:0;top:1110px;width:1200px;height:737px;background:linear-gradient(180deg,#86c340,#72b234);clip-path:polygon(0 205px,1200px 0,1200px 737px,0 737px)}
.services-title{left:0;width:1200px;top:1344px;text-align:center;font-size:34px;color:var(--white)}
.card{position:absolute;top:1415px;width:248px;height:268px}
.card .photo{width:100%;height:100%}
.card span{position:absolute;left:28px;bottom:26px;font-family:"Michroma",sans-serif;font-size:16px;line-height:19px;color:var(--white);text-transform:uppercase}
.card .go{position:absolute;right:18px;bottom:-18px;width:38px;height:38px;background:var(--slate);display:flex;align-items:center;justify-content:center}
.card .go.active{background:#f7941d}
.btn-white{background:var(--white);color:var(--slate)}

/* why */
.why-title{left:0;width:1200px;top:1928px;text-align:center;font-size:34px;color:var(--green-dark)}
.trunk{left:406px;top:2009px;width:388px;height:388px;border-radius:50%;background:radial-gradient(circle,#f2e4cf 0 62%,#a8663a 66%,#6b3b1d 100%);box-shadow:0 18px 30px rgba(0,0,0,.2)}
.trunk-face{left:444px;top:2047px;width:312px;height:312px;border-radius:50%;background:var(--white);display:flex;align-items:center;justify-content:center;font-family:"Montserrat",sans-serif;font-weight:700;font-size:30px;color:var(--green)}
.feat{position:absolute;font-family:"Michroma",sans-serif;font-size:16px;line-height:19px;color:var(--green-dark);text-transform:uppercase}
.feat.left{right:891px;text-align:right}
.feat.right{left:887px}
.feat-icon{position:absolute;width:46px;height:46px}
.rule{position:absolute;height:0;border-top:1px dashed #9fcf6a}

/* call */
.call{left:0;top:2493px;width:594px;height:496px;background:var(--cream)}
.call-photo{left:594px;top:2493px;width:606px;height:496px;background:linear-gradient(120deg,#5d8d2f,#a4c45c 55%,#3e6f8f 75%,#c9d96a)}
.call-title{left:87px;top:2578px;font-size:36px;color:var(--green-dark)}
.call-sub{left:87px;top:2640px;font-size:14px;line-height:22px;font-weight:600;color:var(--green-dark);text-transform:uppercase}
.phone-box{left:87px;top:2695px;width:455px;height:120px;border-radius:20px;background:var(--cream-deep)}
.phones{left:222px;top:2713px;font-size:27px;line-height:36px;color:var(--green-dark);font-weight:500}

/* blog */
.blog-title{left:0;width:1200px;top:3078px;text-align:center;font-size:34px;color:var(--green-dark)}
.post{position:absolute;top:3151px;width:291px;height:379px;background:var(--white);box-shadow:0 8px 24px rgba(0,0,0,.08)}
.post .photo{height:230px}
.post h3{margin:28px 22px 8px;font-family:"Michroma",sans-serif;font-size:15px;color:var(--green-dark);font-weight:400}
.post .date{margin:0 22px 12px;font-size:11px;display:flex;gap:6px;align-items:center}
.post p{margin:0 22px;font-size:13px;line-height:18px}

/* footer */
.silhouette{left:0;top:3640px;width:1200px;height:160px;background:linear-gradient(180deg,rgba(122,82,41,0) 0%,rgba(122,82,41,.35) 60%,var(--brown) 100%)}
.footer{left:0;top:3793px;width:1200px;height:434px;background:var(--brown);color:#f1e6d6}
.f-logo{left:141px;top:3905px;display:flex;align-items:center;gap:16px}
.f-logo .logo-name{color:var(--white);font-size:30px}
.f-logo .logo-mark{width:62px;height:62px}
.f-note{left:141px;top:3996px;width:330px;font-size:12px;line-height:19px}
.news{left:141px;top:4043px;width:383px;height:46px;border-radius:24px;background:var(--white);display:flex;overflow:hidden}
.news span{flex:1;padding-left:18px;display:flex;align-items:center;font-size:12px;color:#666}
.news b{width:110px;background:var(--orange);color:var(--white);font-size:12px;display:flex;align-items:center;justify-content:center}
.f-col{position:absolute;top:3882px;font-size:12px;line-height:35.6px}
.f-col a{display:block;color:inherit;text-decoration:none}
.f-col .dot{display:inline-block;width:20px;height:20px;border-radius:50%;background:rgba(255,255,255,.18);vertical-align:middle;margin-right:14px}
.f-rule{left:141px;top:4171px;width:918px;border-top:1px solid rgba(255,255,255,.2)}
.copy{left:0;width:1200px;top:4197px;text-align:center;font-size:12px}
.chat{left:1112px;top:4143px;width:60px;height:60px;border-radius:50%;background:var(--green);display:flex;align-items:center;justify-content:center}
</style>
</head>
<body>

<!-- hero -->
<div class="abs hero-bg" role="img" aria-label="Arborist in safety gear cutting a branch with a chainsaw against a blue sky"></div>
<div class="abs logo"><div class="logo-mark"></div><div class="logo-name">Verdell<br><span style="font-size:16px;color:var(--green)">Tree Care</span></div></div>
<nav class="abs nav">
  <a style="left:0;top:-3px"><svg width="18" height="18" viewBox="0 0 24 24"><path d="M3 11L12 3l9 8v10h-6v-6H9v6H3z" fill="#f7941d"/></svg></a>
  <a style="left:35px">About Us</a>
  <a style="left:144px">Our Services</a>
  <a style="left:278px">Latest Blog</a>
  <a style="left:404px">Contact Us</a>
</nav>
<a class="btn" style="left:937px;top:23px;width:174px;height:46px">Request Free Quote</a>
<h1 class="abs display hero-title">Call Verdell Tree<br>Care Needs</h1>
<p class="abs hero-sub">Serving Brookhaven and surrounding areas</p>
<a class="btn" style="left:500px;top:345px;width:200px;height:51px">Request Free Quote</a>
<svg class="abs" style="left:586px;top:630px" width="28" height="36" viewBox="0 0 28 36"><path d="M14 2v30M3 22l11 11 11-11" stroke="var(--slate)" stroke-width="2" fill="none"/></svg>

<!-- about -->
<div class="abs about-photo" role="img" aria-label="Gardener in a cap trimming a hedge with electric shears"></div>
<h2 class="abs display about-title">Who We Are</h2>
<div class="abs about-text">
  <p>At Verdell Tree Care, we are more than just a tree service company, we are stewards of our beautiful trees. With a passion deeply rooted in arboriculture, we embark on a mission to promote the health, beauty, and safety of your trees and landscapes.</p>
  <p>Whether it's expert tree trimming to enhance aesthetics, meticulous tree removal to mitigate hazards, or comprehensive tree health assessments to ensure safety, we approach each task with unwavering dedication and attention to detail.</p>
</div>

<!-- services -->
<div class="abs services" role="img" aria-label="Green grass texture background"></div>
<h2 class="abs display services-title">Verdell Tree Care</h2>
<div class="card" style="left:89px"><div class="photo" role="img" aria-label="Worker trimming branches with long loppers" style="background:linear-gradient(160deg,#6e9f4a,#b8cfa0 60%,#8a8f86)"></div><span>Tree<br>Triming</span><div class="go"><svg width="10" height="14" viewBox="0 0 10 14"><path d="M2 1l6 6-6 6" stroke="#fff" stroke-width="2" fill="none"/></svg></div></div>
<div class="card" style="left:347px"><div class="photo" role="img" aria-label="Arborist with helmet cutting a tree trunk" style="background:linear-gradient(160deg,#7a6a4c,#b9c47a 55%,#4e6a2c)"></div><span>Tree<br>Removal</span><div class="go active"><svg width="10" height="14" viewBox="0 0 10 14"><path d="M2 1l6 6-6 6" stroke="#fff" stroke-width="2" fill="none"/></svg></div></div>
<div class="card" style="left:605px"><div class="photo" role="img" aria-label="Excavator clearing trees in a forest" style="background:linear-gradient(160deg,#5e7448,#c08a3a 55%,#4b3f2c)"></div><span>Tree<br>Clearing</span><div class="go"><svg width="10" height="14" viewBox="0 0 10 14"><path d="M2 1l6 6-6 6" stroke="#fff" stroke-width="2" fill="none"/></svg></div></div>
<div class="card" style="left:863px"><div class="photo" role="img" aria-label="Worker in orange shirt pruning a young tree" style="background:linear-gradient(160deg,#8a9a4a,#d9803a 55%,#4e5f2a)"></div><span>Tree<br>Pruning</span><div class="go"><svg width="10" height="14" viewBox="0 0 10 14"><path d="M2 1l6 6-6 6" stroke="#fff" stroke-width="2" fill="none"/></svg></div></div>
<a class="btn btn-white" style="left:512px;top:1726px;width:176px;height:46px;font-weight:600;font-size:11px">View All Services</a>

<!-- why -->
<h2 class="abs display why-title">Why Choose Us?</h2>
<div class="abs trunk" role="img" aria-label="Cross section of a tree trunk"></div>
<div class="abs trunk-face">Verdell</div>

<div class="feat left" style="top:2064px">Licensed and<br>insured</div>
<div class="feat left" style="top:2184px">24-Hours<br>emergency service</div>
<div class="feat left" style="top:2304px">Locally owned<br>&amp; operated</div>
<div class="feat right" style="top:2064px">Professional<br>work</div>
<div class="feat right" style="top:2184px">Safety is our<br>no.1 priority</div>
<div class="feat right" style="top:2304px">Licensed arborist<br>on staff</div>

<svg class="feat-icon" style="left:335px;top:2060px" viewBox="0 0 46 46" fill="none" stroke="var(--green-dark)" stroke-width="2"><rect x="8" y="6" width="30" height="36" rx="2"/><path d="M14 16h18M14 22h18M14 28h12" /><circle cx="32" cy="34" r="4" stroke="var(--green)"/></svg>
<svg class="feat-icon" style="left:335px;top:2180px" viewBox="0 0 46 46" fill="none" stroke="var(--green-dark)" stroke-width="2"><circle cx="23" cy="23" r="17"/><path d="M23 12v11l7 5" stroke="var(--green)"/></svg>
<svg class="feat-icon" style="left:335px;top:2300px" viewBox="0 0 46 46" fill="none" stroke="var(--green-dark)" stroke-width="2"><path d="M6 24l10-10 8 6 8-6 8 10-16 14z"/><path d="M16 26l6 6" stroke="var(--green)"/></svg>
<svg class="feat-icon" style="left:824px;top:2060px" viewBox="0 0 46 46" fill="none" stroke="var(--green-dark)" stroke-width="2"><path d="M14 6l10 16H4z"/><path d="M14 22v16"/><circle cx="30" cy="28" r="8" stroke="var(--green)"/></svg>
<svg class="feat-icon" style="left:824px;top:2180px" viewBox="0 0 46 46" fill="none" stroke="var(--green-dark)" stroke-width="2"><path d="M23 4l13 5v10c0 9-6 15-13 18-7-3-13-9-13-18V9z"/><path d="M17 20l5 5 8-9" stroke="var(--green)"/></svg>
<svg class="feat-icon" style="left:818px;top:2300px" viewBox="0 0 46 46" fill="none" stroke="var(--green-dark)" stroke-width="2"><circle cx="14" cy="16" r="5"/><circle cx="32" cy="16" r="5"/><circle cx="23" cy="10" r="5" stroke="var(--green)"/><path d="M4 40v-8a10 10 0 0 1 20 0v8M22 40v-8a10 10 0 0 1 20 0v8"/></svg>

<div class="rule" style="left:89px;top:2143px;width:223px"></div>
<div class="rule" style="left:89px;top:2263px;width:223px"></div>
<div class="rule" style="left:826px;top:2143px;width:285px"></div>
<div class="rule" style="left:826px;top:2263px;width:285px"></div>

<!-- call -->
<div class="abs call"></div>
<div class="abs call-photo" role="img" aria-label="Gardener in gloves trimming a hedge with a power trimmer"></div>
<h2 class="abs display call-title">Call Us Today</h2>
<p class="abs call-sub">To see how we can help you with<br>all of your tree needs</p>
<div class="abs phone-box"></div>
<svg class="abs" style="left:130px;top:2720px" width="72" height="70" viewBox="0 0 72 70" fill="none" stroke="var(--green-dark)" stroke-width="3"><path d="M6 24c0-12 60-12 60 0v6H50v-8H22v8H6z"/><path d="M16 32l-6 30h52l-6-30z"/><circle cx="36" cy="46" r="8" stroke="var(--green)"/></svg>
<div class="abs phones">(555) 214-0387<br>(555) 730-4162</div>
<a class="btn" style="left:90px;top:2851px;width:325px;height:51px;font-size:11px">Call Marlowe for a free estimate</a>

<!-- blog -->
<h2 class="abs display blog-title">From the Blog</h2>
<article class="post" style="left:149px"><div class="photo" role="img" aria-label="Forestry mulcher machine among cut logs" style="background:linear-gradient(170deg,#6c8a3e,#3d3a5c 50%,#a06a3a)"></div><h3>Blog Heading Here</h3><div class="date"><svg width="11" height="11" viewBox="0 0 11 11"><rect x="1" y="2" width="9" height="8" fill="none" stroke="var(--green)"/></svg>10-03-2024</div><p>Aenean sollicitudin, lorem bibendum auctor nisi elit consequat ipsum.</p></article>
<article class="post" style="left:455px"><div class="photo" role="img" aria-label="Chainsaw cutting into a large tree trunk" style="background:linear-gradient(90deg,#7fa654,#8a7a62 45%,#6a5a48 60%,#9dbb6a)"></div><h3>Blog Heading Here</h3><div class="date"><svg width="11" height="11" viewBox="0 0 11 11"><rect x="1" y="2" width="9" height="8" fill="none" stroke="var(--green)"/></svg>10-03-2024</div><p>Aenean sollicitudin, lorem bibendum auctor nisi elit consequat ipsum.</p></article>
<article class="post" style="left:757px"><div class="photo" role="img" aria-label="Red chainsaw sawing a branch with flying sawdust" style="background:linear-gradient(150deg,#6b6a50,#d24a2a 50%,#8aa86a)"></div><h3>Blog Heading Here</h3><div class="date"><svg width="11" height="11" viewBox="0 0 11 11"><rect x="1" y="2" width="9" height="8" fill="none" stroke="var(--green)"/></svg>10-03-2024</div><p>Aenean sollicitudin, lorem bibendum auctor nisi elit consequat ipsum.</p></article>
<a class="btn" style="left:512px;top:3580px;width:176px;height:46px;font-size:11px">View All Blogs</a>

<!-- footer -->
<div class="abs silhouette" role="img" aria-label="Silhouettes of tree workers, trees and equipment on the horizon"></div>
<footer class="abs footer"></footer>
<div class="abs f-logo"><div class="logo-mark"></div><div class="logo-name">Verdell<br><span style="font-size:19px;color:var(--green)">Tree Care</span></div></div>
<p class="abs f-note">Get our monthly newsletter and marketing tips, straight to your inbox</p>
<div class="abs news"><span>Enter your email</span><b>Subscribe</b></div>
<div class="f-col" style="left:616px;color:#f1e6d6"><a>Home</a><a>About Us</a><a>Our Services</a><a>Latest Blog</a><a>Contact Us</a><a>Get Free Estimate</a></div>
<div class="f-col" style="left:791px;color:#f1e6d6"><a>Have feedback?</a><a>Let us know!</a><a>Privacy Policy</a><a>Terms of Use</a></div>
<div class="f-col" style="left:963px;color:#f1e6d6"><a><i class="dot"></i>Network</a><a><i class="dot"></i>Photos</a><a><i class="dot"></i>Clips</a><a><i class="dot"></i>Community</a></div>
<div class="abs f-rule"></div>
<p class="abs copy">© 2024 Verdell Tree Care. All rights reserved.</p>
<div class="abs chat"><svg width="30" height="26" viewBox="0 0 30 26"><path d="M3 3h24v15H12l-6 5v-5H3z" fill="#fff"/><circle cx="10" cy="10.5" r="1.6" fill="var(--green)"/><circle cx="15" cy="10.5" r="1.6" fill="var(--green)"/><circle cx="20" cy="10.5" r="1.6" fill="var(--green)"/></svg></div>

</body>
</html>
```